Enterprise Application UI beautification

We have an enterprise application that is being redesigned. A screenshot from the new UX/UI is provided. The current UI design is OK but we would like it to look better. The key goals of the UI are to look like a premium product (think luxury brand) and for it to be visually very appealing/attractive. When people see the UI we want them to have a significant, positive reaction. They should "ooh" and "ahh". This is a product sold to large enterprises, not consumers. The current UI is a little plain. The colors we want to use are blue, yellow, black, white and gray. We probably don't want different colors but feel free to use any variations within or close to that color scheme that you see fit. Also feel free to modify the spacing, icons, widgets, tables, fonts, etc.

Target Market(s)

Large enterprise customers (Keystone 300).

Number of Pages Required

1 page

Font styles to use
Sans Serif

Colors
3277b5

Requirements
Must have
• A premium feel.

```html
<!DOCTYPE html>
<html lang="en">
<head>
<meta charset="utf-8">
<title>Data Sources</title>
<link rel="stylesheet" href="https://fonts.googleapis.com/css2?family=Montserrat:wght@400;500;600&display=swap">
<style>
:root{
  --accent:#2b87d1;
  --accent-dark:#3277b5;
  --ink:#1d2330;
  --muted:#4f5665;
  --line:#dfe3e8;
  --sidebar:#16181b;
  --panel:#ffffff;
  --page:#f6f8fa;
  --slate:#474a6b;
  --danger:#e5383b;
  --green:#3cc04a;
}
*{box-sizing:border-box;margin:0;padding:0}
html,body{width:1200px;height:740px;overflow:hidden}
body{font-family:"Montserrat",sans-serif;background:var(--page);color:var(--ink);display:flex}
svg{display:block}
.ico{width:14px;height:14px;fill:none;stroke:currentColor;stroke-width:1.4;stroke-linecap:round;stroke-linejoin:round}

.sidebar{width:62px;background:var(--sidebar);display:flex;flex-direction:column;align-items:center;color:#fff}
.brand{height:70px;display:flex;align-items:center;justify-content:center;font-weight:600;font-size:11px;letter-spacing:.5px;color:var(--accent)}
.nav-item{width:62px;height:63px;display:flex;align-items:center;justify-content:center;margin-top:14px}
.nav-item .ico{width:22px;height:22px}
.nav-item.active{background:var(--accent)}

.sources{width:250px;background:var(--panel);margin-top:62px;display:flex;flex-direction:column}
.sources-head{display:flex;justify-content:space-between;align-items:center;padding:14px 19px 0}
h2{font-size:16px;font-weight:500;color:var(--accent)}
.btn-add{display:flex;align-items:center;gap:5px;background:linear-gradient(#3a95de,#2a7dc8);color:#fff;border-radius:14px;font-size:10px;padding:5px 9px;box-shadow:0 2px 6px rgba(43,135,209,.35)}
.btn-add .ico{width:10px;height:10px;stroke-width:2}
.search{margin:18px 19px 15px;height:27px;border:1px solid #c8ccd2;border-radius:14px;display:flex;align-items:center;justify-content:space-between;padding:0 8px 0 9px;font-size:9.5px;color:#8a9099}
.search .ico{color:var(--accent);width:15px;height:15px}
.source-list{list-style:none}
.source{height:61px;border-bottom:1px solid var(--line);padding:13px 19px 0;margin-right:9px}
.source b{display:block;font-weight:500;font-size:11.5px;white-space:nowrap}
.source span{font-size:8.5px;color:var(--accent)}
.source.active{background:linear-gradient(90deg,#3a92d9,#2470b4);color:#fff;border:0}
.source.active span{color:#dbeaf7}

.main{flex:1;display:flex;flex-direction:column;padding:0 25px}
.topbar{height:62px;display:flex;justify-content:space-between;align-items:center;font-size:11px;margin-left:-50px}
.crumbs{display:flex;align-items:center;gap:6px;color:var(--accent)}
.user{display:flex;align-items:center;gap:5px;color:var(--ink)}
.title-row{display:flex;justify-content:space-between;align-items:center;height:32px}
.title-row h1{font-size:16px;font-weight:600;color:var(--accent)}
.actions{display:flex;gap:40px;font-size:11px;color:var(--accent)}
.actions a{display:flex;align-items:center;gap:5px}
.info{background:var(--panel);margin-top:10px;display:grid;grid-template-columns:1fr 1fr;gap:0 19px;padding:0 19px 0 12px;box-shadow:0 2px 8px rgba(30,50,80,.06)}
.info dl{display:grid;grid-template-columns:251px 1fr}
.info-right dl{grid-template-columns:210px 1fr}
.info dt,.info dd{height:35px;display:flex;align-items:center;border-bottom:1px solid var(--line);font-size:10px;white-space:nowrap}
.info dt{padding-left:10px;color:var(--muted)}
.info dd{color:var(--accent)}
.info dl > :nth-last-child(-n+2){border-bottom:0}
.info-right dl > :nth-last-child(-n+2){border-bottom:1px solid var(--line)}

.objects-head{display:flex;align-items:center;gap:38px;margin:21px 0 8px}
.objects{background:var(--panel);box-shadow:0 2px 8px rgba(30,50,80,.06)}
.object{height:35px;display:flex;align-items:center;gap:8px;padding-left:11px;border-bottom:1px solid var(--line);font-size:12px;font-weight:500;color:var(--muted)}
.toggle{width:14px;height:14px;border:1px solid var(--accent);display:flex;align-items:center;justify-content:center;color:var(--accent)}
.toggle .ico{width:10px;height:10px}
.x{color:var(--danger);font-size:13px}
.object.open{background:var(--slate);color:#fff;border:0}
.object.open .fields-add{margin-left:auto;margin-right:17px;display:flex;gap:8px;font-size:12px}
.fields-add i{font-style:normal;color:var(--green);font-weight:400}
.fields{background:#f1f5fa;padding:0 17px 4px 0;position:relative}
.fields::before{content:"";position:absolute;left:19px;top:14px;bottom:14px;border-left:1px solid var(--slate)}
.fields::after{content:"";position:absolute;left:16px;top:11px;width:7px;height:7px;border-radius:50%;background:var(--slate)}
.frow{display:grid;grid-template-columns:163px 184px 155px 113px 125px 1fr;margin-left:37px;height:37px;align-items:center;border-bottom:1px solid var(--line);font-size:9.5px;color:var(--muted)}
.frow:last-child{border-bottom:0}
.frow.head{font-size:11px;font-weight:500;color:var(--ink);height:31px}
.rules,.sens,.acts{display:flex;align-items:center;gap:9px}
.rules .ico{width:12px;height:12px}
.rules .letter{font-size:16px;color:var(--accent-dark);line-height:1}
.caret{width:0;height:0;border-left:4px solid var(--ink);border-top:4px solid transparent;border-bottom:4px solid transparent}
.caret.hot{border-left-color:#f06a1d}
.pk{display:flex;padding-left:28px}
.box{width:14px;height:14px;background:#b8c7d8;border:1px solid #9fb1c6}
.box.on{background:var(--accent-dark);border-color:var(--accent-dark);color:#fff;display:flex;align-items:center;justify-content:center}
.sens{gap:20px;padding-left:6px;color:var(--muted)}
.acts{justify-content:flex-end;gap:18px}
.edit{color:var(--accent)}
.del{color:var(--danger)}
</style>
</head>
<body>
<svg width="0" height="0" style="position:absolute">
  <defs>
    <symbol id="i-search" viewBox="0 0 16 16"><circle cx="7" cy="7" r="5"/><path d="M11 11l4 4"/></symbol>
    <symbol id="i-copy" viewBox="0 0 16 16"><rect x="5" y="2" width="9" height="9"/><path d="M2 5v9h9"/></symbol>
    <symbol id="i-nodes" viewBox="0 0 16 16"><circle cx="8" cy="4" r="2"/><circle cx="3.5" cy="12" r="2"/><circle cx="12.5" cy="12" r="2"/><path d="M7 6l-2.5 4M9 6l2.5 4M5.5 12h5"/></symbol>
    <symbol id="i-target" viewBox="0 0 16 16"><circle cx="8" cy="8" r="5"/><path d="M8 1v3M8 12v3M1 8h3M12 8h3"/></symbol>
    <symbol id="i-plus" viewBox="0 0 16 16"><path d="M8 2v12M2 8h12"/></symbol>
    <symbol id="i-minus" viewBox="0 0 16 16"><path d="M2 8h12"/></symbol>
    <symbol id="i-pen" viewBox="0 0 16 16"><path d="M3 13l1-4 7-7 3 3-7 7z M10 3l3 3"/></symbol>
    <symbol id="i-trash" viewBox="0 0 16 16"><path d="M3 4h10M6 4V2h4v2M4 4l1 10h6l1-10M7 7v5M9 7v5"/></symbol>
    <symbol id="i-doc" viewBox="0 0 16 16"><rect x="4" y="2" width="8" height="12" rx="1"/><path d="M8 6v4M6 8h4"/></symbol>
    <symbol id="i-card" viewBox="0 0 16 16"><rect x="2" y="4" width="12" height="8"/><path d="M4 8h4"/></symbol>
    <symbol id="i-user" viewBox="0 0 16 16"><circle cx="8" cy="5" r="3"/><path d="M3 14c0-3 2-5 5-5s5 2 5 5z"/></symbol>
    <symbol id="i-tick" viewBox="0 0 16 16"><path d="M3 8l3 3 7-7"/></symbol>
  </defs>
</svg>

<nav class="sidebar">
  <div class="brand">AERIX</div>
  <div class="nav-item"><svg class="ico" viewBox="0 0 24 24"><circle cx="12" cy="6" r="2.5"/><circle cx="5" cy="9" r="2"/><circle cx="19" cy="9" r="2"/><path d="M8 20v-5a4 4 0 018 0v5M2 19v-3a3 3 0 013-3M22 19v-3a3 3 0 00-3-3"/></svg></div>
  <div class="nav-item"><svg class="ico" viewBox="0 0 24 24"><path d="M6 18h12a4 4 0 000-8 6 6 0 00-11-1 4.5 4.5 0 00-1 9z"/></svg></div>
  <div class="nav-item active"><svg class="ico" viewBox="0 0 24 24"><rect x="5" y="3" width="13" height="15" rx="2"/><path d="M3 7v12a2 2 0 002 2h11M8 14h7"/></svg></div>
  <div class="nav-item"><svg class="ico" viewBox="0 0 24 24"><rect x="5" y="4" width="14" height="17" rx="2"/><path d="M9 3h6v3H9zM8 10h8M8 14h5M12 18l2 2 4-4"/></svg></div>
  <div class="nav-item"><svg class="ico" viewBox="0 0 24 24"><rect x="3" y="5" width="18" height="16" rx="2"/><path d="M3 10h18M8 3v4M16 3v4"/><circle cx="16" cy="16" r="3"/></svg></div>
  <div class="nav-item"><svg class="ico" viewBox="0 0 24 24"><circle cx="6" cy="5" r="2"/><circle cx="18" cy="19" r="2"/><circle cx="12" cy="19" r="2"/><path d="M6 7v4a4 4 0 004 4h2M14 5h4v4M18 5l-6 6"/></svg></div>
</nav>

<aside class="sources">
  <div class="sources-head">
    <h2>Data Sources</h2>
    <span class="btn-add"><svg class="ico"><use href="#i-plus"/></svg>ADD</span>
  </div>
  <div class="search">Search...<svg class="ico"><use href="#i-search"/></svg></div>
  <ul class="source-list">
    <li class="source active"><b>Skyforce - Sandbox</b><span>Skyforce.io</span></li>
    <li class="source"><b>PostBase Test 1 (administration)</b><span>PostBase</span></li>
    <li class="source"><b>PostBase Test 2 (administration)</b><span>PostBase</span></li>
    <li class="source"><b>Sadge</b><span>Skyforce.io</span></li>
    <li class="source"><b>Skyforce Test 1 (masterd ev)</b><span>PostBase</span></li>
    <li class="source"><b>SKYF - Field Entry Test</b><span>Skyforce.io</span></li>
    <li class="source"><b>SKYF 44</b><span>Skyforce.io</span></li>
    <li class="source"><b>SKYF 66</b><span>Skyforce.io</span></li>
    <li class="source"><b>SKYF - Field Entry Test</b><span>Skyforce.io</span></li>
  </ul>
</aside>

<main class="main">
  <header class="topbar">
    <div class="crumbs"><svg class="ico" viewBox="0 0 16 16"><path d="M2 12a6 6 0 1112 0M8 10l3-4"/></svg>Dashboard&nbsp;-&nbsp;&nbsp;Menu Name</div>
    <div class="user"><svg class="ico" viewBox="0 0 16 16"><circle cx="8" cy="8" r="2.5"/><circle cx="8" cy="8" r="6"/></svg>Dana Reyes <svg class="ico" style="width:9px" viewBox="0 0 16 16"><path d="M3 6l5 5 5-5"/></svg></div>
  </header>

  <div class="title-row">
    <h1>Skyforce - Sandbox</h1>
    <div class="actions">
      <a><svg class="ico"><use href="#i-pen"/></svg>Edit</a>
      <a><svg class="ico" viewBox="0 0 16 16"><path d="M13 8a5 5 0 11-2-4M11 1v3h3"/></svg>Clone</a>
      <a><svg class="ico"><use href="#i-trash"/></svg>Delete</a>
      <a><svg class="ico" viewBox="0 0 16 16"><path d="M9 1L4 9h4l-1 6 5-8H8z"/></svg>Test Connection</a>
    </div>
  </div>

  <section class="info">
    <dl>
      <dt>Date Source Name :</dt><dd>Skyforce - Sandbox</dd>
      <dt>Date Source Type :</dt><dd>Application</dd>
      <dt>Status :</dt><dd>Active</dd>
      <dt>Created By :</dt><dd>harbor.test</dd>
      <dt>Last Updated By :</dt><dd>harbor.test</dd>
    </dl>
    <div class="info-right"><dl>
      <dt>User Name :</dt><dd>masterdev@dev.northwinddata.net</dd>
      <dt>Security Token :</dt><dd>tadkaji4234ifndkn3</dd>
      <dt>Environment Type :</dt><dd>Production</dd>
      <dt>Connected App :</dt><dd>No</dd>
    </dl></div>
  </section>

  <div class="objects-head">
    <h2>Data Objects</h2>
    <span class="btn-add"><svg class="ico"><use href="#i-plus"/></svg>ADD</span>
  </div>

  <section class="objects">
    <div class="object"><span class="toggle"><svg class="ico"><use href="#i-plus"/></svg></span>Account <span class="x">✕</span></div>
    <div class="object"><span class="toggle"><svg class="ico"><use href="#i-plus"/></svg></span>Asset <span class="x">✕</span></div>
    <div class="object"><span class="toggle"><svg class="ico"><use href="#i-plus"/></svg></span>Asset Relationship <span class="x">✕</span></div>
    <div class="object"><span class="toggle"><svg class="ico"><use href="#i-plus"/></svg></span>Asset Token Event <span class="x">✕</span></div>
    <div class="object open"><span class="toggle"><svg class="ico"><use href="#i-minus"/></svg></span>Case <span class="x">✕</span><span class="fields-add">Fields <i>+ Add</i></span></div>

    <div class="fields">
      <div class="frow head"><span>Field Name</span><span>Data Type</span><span>Rule Types</span><span>Primary Key</span><span>Sensitive Data</span><span style="text-align:right">Actions</span></div>

      <div class="frow"><span>Account Description</span><span>Common Text</span>
        <span class="rules"><span class="letter">a</span><svg class="ico"><use href="#i-search"/></svg><svg class="ico"><use href="#i-copy"/></svg><svg class="ico"><use href="#i-nodes"/></svg><svg class="ico"><use href="#i-target"/></svg><span class="caret"></span></span>
        <span class="pk"><span class="box on"><svg class="ico" style="width:10px;height:10px;stroke-width:2"><use href="#i-tick"/></svg></span></span>
        <span class="sens"><svg class="ico"><use href="#i-doc"/></svg><svg class="ico"><use href="#i-card"/></svg><svg class="ico"><use href="#i-user"/></svg></span>
        <span class="acts"><svg class="ico edit"><use href="#i-pen"/></svg><svg class="ico del"><use href="#i-trash"/></svg></span></div>

      <div class="frow"><span>Account Fax</span><span>Address. Address Line 3</span>
        <span class="rules"><span class="letter">a</span><svg class="ico" style="color:#e2a800"><use href="#i-search"/></svg><svg class="ico"><use href="#i-copy"/></svg><svg class="ico"><use href="#i-nodes"/></svg><svg class="ico" style="color:#1fb5c7"><use href="#i-target"/></svg><span class="caret"></span></span>
        <span class="pk"><span class="box"></span></span><span></span>
        <span class="acts"><svg class="ico edit"><use href="#i-pen"/></svg><svg class="ico del"><use href="#i-trash"/></svg></span></div>

      <div class="frow"><span>Account ID</span><span>Common ID</span>
        <span class="rules"><span class="letter">a</span><svg class="ico"><use href="#i-search"/></svg><svg class="ico" style="color:var(--green)"><use href="#i-copy"/></svg><svg class="ico"><use href="#i-nodes"/></svg><svg class="ico"><use href="#i-target"/></svg><span class="caret hot"></span></span>
        <span class="pk"><span class="box"></span></span>
        <span class="sens"><svg class="ico"><use href="#i-doc"/></svg><svg class="ico"><use href="#i-card"/></svg><svg class="ico"><use href="#i-user"/></svg></span>
        <span class="acts"><svg class="ico edit"><use href="#i-pen"/></svg><svg class="ico del"><use href="#i-trash"/></svg></span></div>

      <div class="frow"><span>Account Name</span><span>Address. Address Line 2</span>
        <span class="rules"><span class="letter">a</span><svg class="ico"><use href="#i-search"/></svg><svg class="ico"><use href="#i-copy"/></svg><svg class="ico" style="color:var(--danger)"><use href="#i-nodes"/></svg><svg class="ico"><use href="#i-target"/></svg><span class="caret"></span></span>
        <span class="pk"><span class="box"></span></span><span></span>
        <span class="acts"><svg class="ico edit"><use href="#i-pen"/></svg><svg class="ico del"><use href="#i-trash"/></svg></span></div>
    </div>
  </section>
</main>
</body>
</html>
```